Weightloss company needs Business Card

We want a business card that is clean and professional, yet portrays that we are a friendly, innovative, and versatile program designed to fit the needs of our clients.
I would like there to be 2 sides, one side having an appointment card, and the other side containing the logo and business information. There can be decorations on both sides. The logo is attached.

Target Market(s)

Men and women 40-60

Industry/Entity Type

Business

Contact Information for Business Card

Font styles to use
Sans Serif

Requirements
Must have
• The logo, space for business information
Nice to have
• The colors in the logo
Should not have
• No pictures of people or food

```html
<!DOCTYPE html>
<html lang="en">
<head>
<meta charset="UTF-8">
<title>Brightturn Wellness Business Card</title>
<link rel="stylesheet" href="https://fonts.googleapis.com/css2?family=Open+Sans:wght@400;600;700&display=swap">
<style>
  :root {
    --page-bg: #ecebe8;
    --card-white: #ffffff;
    --card-grey: #d9dadc;
    --brand-red: #e4173e;
    --brand-cyan: #27c9ee;
    --brand-cyan-deep: #12a9d6;
    --ink: #3a3a3a;
    --ink-soft: #555a5e;
    --rule: #5a5a5a;
  }
  * { box-sizing: border-box; margin: 0; padding: 0; }
  html, body { width: 1200px; height: 843px; overflow: hidden; }
  body {
    background: var(--page-bg);
    font-family: "Open Sans", sans-serif;
    display: flex;
    align-items: center;
    justify-content: center;
    gap: 30px;
  }
  .card {
    position: relative;
    width: 560px;
    height: 320px;
    border-radius: 18px;
    overflow: hidden;
    box-shadow: 0 10px 28px rgba(0,0,0,0.18);
  }

  /* Appointment side */
  .card-appointment {
    background: linear-gradient(180deg, var(--card-white) 0%, var(--card-white) 55%, var(--card-grey) 100%);
    padding: 34px 34px 0 40px;
    color: var(--ink);
  }
  .appointment-title {
    color: var(--brand-red);
    font-weight: 700;
    font-size: 21px;
    margin-top: 30px;
  }
  .brand-mark {
    position: absolute;
    display: flex;
    align-items: center;
    gap: 8px;
    color: var(--brand-red);
    font-weight: 700;
    white-space: nowrap;
  }
  .brand-mark .dot {
    border-radius: 50%;
    border: 3px solid var(--brand-red);
  }
  .card-appointment .brand-mark { top: 26px; right: 30px; font-size: 19px; }
  .card-appointment .brand-mark .dot { width: 20px; height: 20px; }
  .slot-list { margin-top: 14px; display: flex; flex-direction: column; gap: 22px; }
  .slot {
    display: grid;
    grid-template-columns: 44px 170px 50px 110px auto;
    align-items: end;
    font-size: 14px;
  }
  .slot .line { border-bottom: 1.5px solid var(--rule); height: 16px; margin-right: 14px; }
  .slot .line-time { margin-right: 8px; }
  .slot .ampm { font-size: 14px; }
  .appointment-note {
    position: absolute;
    left: 40px;
    bottom: 22px;
    font-size: 12px;
    font-weight: 600;
    color: var(--ink-soft);
  }

  /* Contact side */
  .card-contact { background: var(--card-white); color: var(--card-white); }
  .card-contact svg.card-bg { position: absolute; inset: 0; }
  .contact-block { position: absolute; left: 30px; top: 34px; }
  .person-name { font-size: 20px; font-weight: 600; letter-spacing: 0.5px; }
  .person-role { font-size: 13px; margin-top: 1px; }
  .address {
    font-size: 13px;
    line-height: 1.4;
    margin-top: 16px;
    padding-bottom: 10px;
    border-bottom: 1px dashed rgba(255,255,255,0.55);
    width: 200px;
  }
  .contact-list { list-style: none; margin-top: 10px; font-size: 13.5px; line-height: 1.55; }
  .contact-list li { display: flex; align-items: center; gap: 10px; }
  .contact-list svg { width: 13px; height: 13px; fill: var(--card-white); flex: none; }
  .card-contact .brand-mark { top: 138px; right: 36px; font-size: 25px; }
  .card-contact .brand-mark .dot { width: 26px; height: 26px; }
</style>
</head>
<body>

  <section class="card card-appointment" aria-label="Appointment side">
    <div class="brand-mark"><span class="dot"></span>Brightturn Wellness</div>
    <h2 class="appointment-title">Next Appointment</h2>
    <div class="slot-list">
      <div class="slot"><span>Date</span><span class="line"></span><span>Time</span><span class="line line-time"></span><span class="ampm">am/pm</span></div>
      <div class="slot"><span>Date</span><span class="line"></span><span>Time</span><span class="line line-time"></span><span class="ampm">am/pm</span></div>
      <div class="slot"><span>Date</span><span class="line"></span><span>Time</span><span class="line line-time"></span><span class="ampm">am/pm</span></div>
    </div>
    <p class="appointment-note">Please give 24 hours notice to cancel or a fee may be charged</p>
  </section>

  <section class="card card-contact" aria-label="Contact side">
    <svg class="card-bg" viewBox="0 0 560 320" preserveAspectRatio="none" aria-hidden="true">
      <defs>
        <linearGradient id="cyanFill" x1="0" y1="0" x2="0" y2="1">
          <stop offset="0" stop-color="var(--brand-cyan)"/>
          <stop offset="1" stop-color="var(--brand-cyan-deep)"/>
        </linearGradient>
        <linearGradient id="whiteFill" x1="0" y1="0" x2="0" y2="1">
          <stop offset="0" stop-color="#ffffff"/>
          <stop offset="0.6" stop-color="#f4f4f5"/>
          <stop offset="1" stop-color="#d6d7d9"/>
        </linearGradient>
      </defs>
      <rect width="560" height="320" fill="url(#whiteFill)"/>
      <path d="M0,0 H300 C250,110 262,230 340,320 H0 Z" fill="url(#cyanFill)"/>
      <path d="M300,0 C250,110 262,230 340,320" fill="none" stroke="var(--brand-red)" stroke-width="6"/>
    </svg>

    <div class="contact-block">
      <h1 class="person-name">DANA WHITFIELD</h1>
      <p class="person-role">CEO/FOUNDER</p>
      <p class="address">2140 Larchmont Road<br>Juneau, Alaska 99801</p>
      <ul class="contact-list">
        <li><svg viewBox="0 0 24 24"><path d="M6.6 10.8a15 15 0 0 0 6.6 6.6l2.2-2.2a1 1 0 0 1 1-.25 11.4 11.4 0 0 0 3.6.57 1 1 0 0 1 1 1V20a1 1 0 0 1-1 1A17 17 0 0 1 3 4a1 1 0 0 1 1-1h3.5a1 1 0 0 1 1 1 11.4 11.4 0 0 0 .57 3.6 1 1 0 0 1-.25 1z"/></svg>907 555 0142</li>
        <li><svg viewBox="0 0 24 24"><path d="M7 1h10a2 2 0 0 1 2 2v18a2 2 0 0 1-2 2H7a2 2 0 0 1-2-2V3a2 2 0 0 1 2-2zm0 4v13h10V5z"/></svg>907 555 0187</li>
        <li><svg viewBox="0 0 24 24"><path d="M6 2h10l2 2v5H6zM3 10h18v9h-3v3H6v-3H3zm5 6v4h8v-4z"/></svg>907 555 0163</li>
        <li><svg viewBox="0 0 24 24"><path d="M2 5h20v14H2zm2 2v.5l8 5 8-5V7z"/></svg>hello@brightturn.com</li>
        <li><svg viewBox="0 0 24 24"><path d="M12 2a10 10 0 1 0 0 20 10 10 0 0 0 0-20zm-1 17.9A8 8 0 0 1 4.1 11H7a14 14 0 0 0 4 8.9zM11 9H4.3A8 8 0 0 1 11 4.1zm2 0V4.1A8 8 0 0 1 19.7 9zm0 2h6.9A8 8 0 0 1 13 19.9z"/></svg>www.brightturn.com</li>
      </ul>
    </div>

    <div class="brand-mark"><span class="dot"></span>Brightturn Wellness</div>
  </section>

</body>
</html>
```